TalkHarbor - Language Coaching Services

Sleek, innovative, trendy design for Language Coaching business.

TalkHarbor is a new UK based company that provides Language Coaching services. We offer highly personalized on-line and face to face language courses. We also impart learning techniques workshops based on the latest neuroscience research for second-language acquisition.

Target Market(s)

See attached info

Industry/Entity Type

Consulting

Contact Information for Business Card

TalkHarbor
DaniaKV@talkharbor.co.uk
TalkHarbor.co.uk
London, UK

Font styles to use
Sans Serif

```html
<!DOCTYPE html>
<html lang="en">
<head>
<meta charset="utf-8">
<title>TalkHarbor Business Card</title>
<link href="https://fonts.googleapis.com/css2?family=Montserrat:wght@400;500;600&family=Roboto:wght@400;500&display=swap" rel="stylesheet">
<style>
  :root {
    --bg: #141414;
    --card: #262626;
    --card-edge: #1e1e1e;
    --brand-blue: #1a9ad6;
    --accent-blue: #19b3ea;
    --text-light: #f2f2f2;
    --text-muted: #d8d8d8;
    --silver: #9a9a9a;
    --rule: #e6e6e6;
  }
  * { margin: 0; padding: 0; box-sizing: border-box; }
  html, body { width: 1200px; height: 900px; overflow: hidden; }
  body {
    background: radial-gradient(ellipse at 50% 30%, #2a2a2a 0%, var(--bg) 70%);
    font-family: "Roboto", Arial, sans-serif;
    position: relative;
  }
  .card {
    position: absolute;
    left: 240px;
    width: 720px;
    height: 380px;
    background: linear-gradient(160deg, #2c2c2c 0%, var(--card) 55%, var(--card-edge) 100%);
    box-shadow: 0 18px 40px rgba(0,0,0,.6);
  }
  .card--services { top: 50px; }
  .card--contact { top: 470px; }

  /* Services side */
  .services-brand {
    position: absolute; top: 34px; left: 0; width: 100%;
    display: flex; flex-direction: column; align-items: center; gap: 12px;
  }
  .brand-ring {
    width: 86px; height: 86px; border-radius: 50%;
    border: 6px solid var(--silver);
  }
  .brand-name {
    font-family: "Montserrat", Arial, sans-serif;
    font-weight: 500;
    letter-spacing: 3px;
    text-transform: uppercase;
  }
  .services-brand .brand-name { font-size: 38px; color: var(--silver); }
  .services-block {
    position: absolute; top: 206px; left: 60px; right: 60px; text-align: center;
  }
  .services-title {
    font-family: "Montserrat", Arial, sans-serif; font-weight: 600;
    color: var(--accent-blue); font-size: 21px; margin-bottom: 2px;
  }
  .services-tagline {
    color: var(--accent-blue); font-size: 17px;
    border-top: 1px solid var(--rule); border-bottom: 1px solid var(--rule);
    padding: 3px 0 5px; margin-bottom: 8px;
  }
  .services-list { color: var(--text-light); font-size: 16px; line-height: 1.6; }
  .sep { color: var(--accent-blue); padding: 0 3px; }

  /* Contact side */
  .contact-brand {
    position: absolute; left: 40px; top: 70px; width: 310px;
    display: flex; flex-direction: column; align-items: center; gap: 16px;
  }
  .contact-brand .brand-ring { width: 130px; height: 130px; border: 9px solid var(--brand-blue); }
  .contact-brand .brand-name { font-size: 40px; color: var(--brand-blue); letter-spacing: 2px; }
  .divider {
    position: absolute; left: 378px; top: 70px; width: 2px; height: 240px; background: var(--rule);
  }
  .contact-info { position: absolute; left: 412px; top: 68px; right: 20px; }
  .person-name {
    font-family: "Montserrat", Arial, sans-serif; font-weight: 600;
    color: var(--accent-blue); font-size: 29px; letter-spacing: 2px; text-transform: uppercase;
  }
  .person-title {
    font-family: "Montserrat", Arial, sans-serif; color: var(--text-light);
    font-size: 18px; letter-spacing: 1px; margin-bottom: 16px;
  }
  .address, .contact-line {
    font-family: "Montserrat", Arial, sans-serif; color: var(--text-light);
    font-size: 18px; letter-spacing: 1.2px; line-height: 1.45;
  }
  .address { margin-bottom: 10px; }
  .contact-line { display: flex; align-items: center; gap: 10px; }
  .contact-line svg { width: 13px; height: 13px; flex: none; }
  .web-domain { color: var(--accent-blue); }
</style>
</head>
<body>
  <section class="card card--services">
    <div class="services-brand">
      <div class="brand-ring"></div>
      <div class="brand-name">TalkHarbor</div>
    </div>
    <div class="services-block">
      <h2 class="services-title">Our Services</h2>
      <p class="services-tagline">We offer highly customized coaching sessions and self-study content.</p>
      <p class="services-list">
        Face to face language coaching sessions<span class="sep">|</span>On-line language coaching sessions<br>
        Personalized Newsletters for self-learners<span class="sep">|</span>Language Learning Techniques Workshops<br>
        Mindful Learning Workshops<span class="sep">|</span>Access to premium content, resources.
      </p>
    </div>
  </section>

  <section class="card card--contact">
    <div class="contact-brand">
      <div class="brand-ring"></div>
      <div class="brand-name">TalkHarbor</div>
    </div>
    <div class="divider"></div>
    <div class="contact-info">
      <h1 class="person-name">Oliver Grant</h1>
      <p class="person-title">Director</p>
      <p class="address">42 Harbour Lane,<br>London, UK, E1 6AN</p>
      <p class="contact-line">
        <svg viewBox="0 0 16 16" aria-hidden="true"><path d="M4 1l3 3-2 2c1 2 3 4 5 5l2-2 3 3-2 3C7 15 1 9 1 3z" fill="var(--brand-blue)"/></svg>
        (020) 555-0147
      </p>
      <p class="contact-line">
        <svg viewBox="0 0 16 16" aria-hidden="true"><rect x="1" y="3" width="14" height="10" fill="none" stroke="var(--brand-blue)" stroke-width="1.5"/><path d="M1 3l7 6 7-6" fill="none" stroke="var(--brand-blue)" stroke-width="1.5"/></svg>
        Info@talkharbor.co.uk
      </p>
      <p class="contact-line">
        <svg viewBox="0 0 16 16" aria-hidden="true"><circle cx="8" cy="8" r="6.5" fill="none" stroke="var(--brand-blue)" stroke-width="1.3"/><ellipse cx="8" cy="8" rx="3" ry="6.5" fill="none" stroke="var(--brand-blue)" stroke-width="1.1"/><path d="M1.5 8h13" stroke="var(--brand-blue)" stroke-width="1.1"/></svg>
        <span>www.<span class="web-domain">talkharbor</span>.co.uk</span>
      </p>
    </div>
  </section>
</body>
</html>
```